4D Cradle Glimpse Luxury Ultrasound Billboard

Design a HIGH-END, MODERN billboard for my private prenatal ultrasound studio, 4D Cradle Glimpse, located in Pace, Florida.
This billboard will be viewed by drivers traveling at highway speeds, so it must be extremely clean, simple, and readable within 6 seconds.
About My Business
4D Cradle Glimpse is a private prenatal ultrasound studio specializing in:
Highest technology 4D/HD Ultrasounds
Early Gender Determination
Pregnancy Confirmation
I have been serving families for nearly 10 years and is known for creating a memorable experience, not just an ultrasound appointment.
Design Style
I DO NOT want:
Flowers
Leaves
Swirls
Glitter
Hearts everywhere
Busy backgrounds
Generic maternity stock graphics
I DO want:
Modern
Luxury
Upscale
Clean
Professional
Eye-catching
Premium medical spa feel
Colors
Use colors from my logo:
LOGO Green ( or a deep green)
Black
White
Soft Gold accents
Images:
Incorporate my professional headshot in a clean, modern way, logo, and the ultrasound images
Text
Keep wording minimal.
Primary Headline ( OPEN TO IDEAS) :
EXAMPLES ( WOULD RATHER SOMETHING MORE CATCHY)
" ADVANCED IMAGING. UNFORGETTABLE MOMENTS"
"MEET YOUR BABY BEFORE BIRTH"
Under headline:
4D Ultrasound • Early Gender • Pregnancy Confirmation
Business Name:
4D Cradle Glimpse
Private Prenatal Ultrasound Studio
Phone Number:
850-471-5923
Important
This billboard must be readable in 5–6 seconds from a moving vehicle.
Less text is better.
The phone number and business name must be visible from a distance.
The design should feel like a premium brand that immediately tells expecting parents:
“This is where I go to see my baby.”
Files Provided
Official logo
Headshot
Ultrasound images
Don’t make this look like a medical office billboard.
Make it look like a luxury baby experience billboard. That’s what separates 4D Cradle Glimpse from hospitals, OB offices, and all the new studios popping up around you. The emotional connection is what gets moms to book. ❤️
Billboard Size - 10.6” x 36”

```html
<!DOCTYPE html>
<html lang="en">
<head>
<meta charset="utf-8">
<title>4D Cradle Glimpse Billboard</title>
<link rel="stylesheet" href="https://fonts.googleapis.com/css2?family=Montserrat:wght@600;700;800&family=Playfair+Display:wght@400&family=Rubik:wght@600&family=Krona+One&display=swap">
<style>
  :root {
    --stage: #e6e7e8;
    --green: #5f6e68;
    --gold: #b8913f;
    --cream: #f8f4ec;
    --white: #ffffff;
    --headshot-tone: #d9c3a8;
    --scan-tone: #8a4a3c;
  }
  html, body {
    margin: 0;
    width: 1200px;
    height: 437px;
    overflow: hidden;
    background: var(--stage);
  }
  .billboard {
    position: absolute;
    left: 76px;
    top: 64px;
    width: 1048px;
    height: 308px;
    box-shadow: 0 2px 8px rgba(0,0,0,0.12);
  }
  .headline-sans { font-family: "Montserrat", sans-serif; font-weight: 800; fill: var(--green); }
  .headline-serif { font-family: "Playfair Display", serif; font-weight: 400; fill: var(--gold); }
  .services { font-family: "Rubik", sans-serif; font-weight: 600; fill: var(--white); font-size: 13px; }
  .phone-number { font-family: "Krona One", sans-serif; fill: var(--white); }
  .brand-name { font-family: "Montserrat", sans-serif; font-weight: 700; fill: var(--green); }
  .brand-tagline { font-family: "Montserrat", sans-serif; font-weight: 600; fill: var(--green); font-size: 7px; }
</style>
</head>
<body>
<svg class="billboard" viewBox="0 0 1048 308" xmlns="http://www.w3.org/2000/svg">
  <defs>
    <linearGradient id="headshotFill" x1="0" y1="0" x2="0" y2="1">
      <stop offset="0" stop-color="#e4cfb4"/>
      <stop offset="0.55" stop-color="var(--headshot-tone)"/>
      <stop offset="1" stop-color="#6f7d62"/>
    </linearGradient>
    <radialGradient id="scanFill" cx="0.5" cy="0.45" r="0.7">
      <stop offset="0" stop-color="#3a1a16"/>
      <stop offset="0.35" stop-color="var(--scan-tone)"/>
      <stop offset="1" stop-color="#b86f5e"/>
    </radialGradient>
    <linearGradient id="creamFill" x1="0" y1="0" x2="0" y2="1">
      <stop offset="0" stop-color="#f6efe2"/>
      <stop offset="1" stop-color="#fbf9f4"/>
    </linearGradient>
  </defs>

  <!-- central cream field -->
  <rect class="field" width="1048" height="308" fill="url(#creamFill)"/>

  <!-- left white panel with gold curve -->
  <path class="side-panel" d="M0,0 L267,0 Q290,190 187,308 L0,308 Z" fill="var(--white)"/>
  <path class="side-panel-edge" d="M267,0 Q290,190 187,308" fill="none" stroke="var(--gold)" stroke-width="2.5"/>

  <!-- bottom phone band -->
  <path class="phone-band" d="M246,246 L1048,252 L1048,308 L187,308 Q224,282 246,246 Z" fill="var(--green)"/>

  <!-- right ultrasound frame -->
  <path class="scan-frame" d="M770,0 L1048,0 L1048,252 L797,246 Q870,118 770,0 Z" fill="var(--green)"/>
  <path class="scan-edge" d="M780,0 Q882,118 808,243" fill="none" stroke="var(--gold)" stroke-width="2"/>
  <path class="scan-image" role="img" aria-label="4D ultrasound image of twin babies face to face"
        d="M789,2 L1043,2 L1043,244 L817,244 Q890,118 789,2 Z" fill="url(#scanFill)"/>
  <line x1="760" y1="0" x2="1048" y2="0" stroke="var(--gold)" stroke-width="2"/>

  <!-- logo block -->
  <g class="brand-lockup">
    <rect x="34" y="11" width="172" height="85" rx="10" fill="var(--white)" stroke="var(--green)" stroke-width="2"/>
    <circle cx="120" cy="32" r="7" fill="var(--gold)"/>
    <text class="brand-name" x="120" y="62" font-size="17" text-anchor="middle">4D Cradle Glimpse</text>
    <line x1="44" y1="72" x2="196" y2="72" stroke="var(--gold)" stroke-width="0.8"/>
    <text class="brand-tagline" x="120" y="86" text-anchor="middle" textLength="132" lengthAdjust="spacingAndGlyphs">PRENATAL ULTRASOUND STUDIO</text>
  </g>

  <!-- headshot -->
  <rect class="headshot" role="img" aria-label="Professional headshot of the studio owner" x="10" y="99" width="160" height="209" rx="70" ry="70" fill="url(#headshotFill)"/>

  <!-- headline -->
  <text class="headline-sans" x="356" y="58" font-size="52" textLength="322" lengthAdjust="spacingAndGlyphs">MEET YOUR</text>
  <text class="headline-serif" x="353" y="159" font-size="120" textLength="338" lengthAdjust="spacingAndGlyphs">BABY</text>
  <text class="headline-sans" x="349" y="196" font-size="39" textLength="326" lengthAdjust="spacingAndGlyphs">BEFORE BIRTH</text>
  <path class="accent-heart" d="M327,182 c-4,-4 -10,-9 -10,-13 c0,-4 5,-6 10,-2 c5,-4 10,-2 10,2 c0,4 -6,9 -10,13 Z" fill="var(--gold)"/>
  <path class="accent-heart" d="M697,182 c-4,-4 -10,-9 -10,-13 c0,-4 5,-6 10,-2 c5,-4 10,-2 10,2 c0,4 -6,9 -10,13 Z" fill="var(--gold)"/>

  <!-- services pill -->
  <rect class="services-pill" x="300" y="210" width="418" height="26" rx="13" fill="var(--green)"/>
  <text class="services" x="509" y="228" text-anchor="middle" textLength="385" lengthAdjust="spacingAndGlyphs">4D Ultrasound <tspan fill="var(--gold)">•</tspan> Early Gender <tspan fill="var(--gold)">•</tspan> Pregnancy Confirmation</text>

  <!-- phone -->
  <circle class="phone-badge" cx="395" cy="281" r="22" fill="var(--gold)"/>
  <path class="phone-icon" d="M386,271 l5,-2 l4,7 l-3,3 q3,6 8,9 l3,-3 l7,4 l-2,5 q-10,2 -17,-7 q-7,-8 -5,-16 Z" fill="none" stroke="var(--white)" stroke-width="2.2" stroke-linejoin="round"/>
  <path d="M399,268 q7,1 9,8 M399,263 q12,1 14,13" fill="none" stroke="var(--white)" stroke-width="1.8" stroke-linecap="round"/>
  <text class="phone-number" x="428" y="300" font-size="45" textLength="523" lengthAdjust="spacingAndGlyphs">850-471-5923</text>
</svg>
</body>
</html>
```